International business needs business cards

Our company, DRV Ventures Inc. is in the business of supplying a range construction products with particular emphasis on CEMENT. We have developed our own brand - TORVAN SUPPLIES - with which to infiltrate the market. We are launching our brand of cement (TORVAN Type IS Cement) into the Caribbean which is unlike anything this market has ever seen. A monopoly has existed here for the past 60-odd years and the market has now opened to allow the importation of other brands and consumers are anxious and ready for change/improvement. We are very excited to be launching and want to make a great first impression. We will be conducting workshops and seminars (from government level to the hardware store owners) and we want our business card to give us the strong, confident introduction that we need.

Target Market(s)

construction; builders; engineers; home owners

Industry/Entity Type

Construction

Contact Information for Business Card

Marisol Depree
CEO
cell # 1 555 4180736
Ground floor,Lindell Plaza Suite 2734
George Town,Grand Cayman
Cayman Islands,KY1-4823
EMAIL: m.depree@drvventuresinc.example
web site drvventuresinc.example

COMPANY: skype info drv.ventures.example

second card
Yvette Brannock-Depree
CFO
CELL# 1 555 607 3941
George Town,Grand Cayman
Cayman Islands,KY1-4823
EMAIL: y.brannockdepree@drvventuresinc.example
website drvventuresinc.example

Requirements
Must have
• Business cards must display BOTH logos - DRV is the company and TORVAN is the brand.

```html
<!DOCTYPE html>
<html lang="en">
<head>
<meta charset="utf-8">
<title>DRV Ventures Inc. – Business Card</title>
<link rel="stylesheet" href="https://fonts.googleapis.com/css2?family=Source+Sans+3:wght@400;600;700&display=swap">
<style>
  :root {
    --backdrop: #8e8e8e;
    --paper: #f3f3f3;
    --maroon: #6b1315;
    --ink: #1c1c1c;
    --ink-soft: #4a4a4a;
    --crest-grey: #4b4b4b;
    --white: #ffffff;
  }
  * { margin: 0; padding: 0; box-sizing: border-box; }
  html, body {
    width: 1105px; height: 1200px; overflow: hidden;
    background: var(--backdrop);
    font-family: "Source Sans 3", "Myriad Pro", Arial, sans-serif;
  }
  .canvas { position: relative; width: 1105px; height: 1200px; }

  .card {
    position: absolute; left: 182px; width: 746px; height: 427px;
  }
  .card--front { top: 119px; background: var(--paper); }
  .card--back  { top: 637px; background: var(--maroon); }

  /* company mark */
  .company-mark {
    position: absolute; left: 41px; top: 41px;
    display: flex; align-items: center; gap: 14px;
  }
  .company-mark__square { width: 100px; height: 100px; background: var(--maroon); }
  .company-mark__name {
    font-weight: 700; font-size: 36px; line-height: 1.05; color: var(--ink);
    width: 190px;
  }

  /* brand mark */
  .brand-mark {
    position: absolute; display: flex; flex-direction: column; align-items: center; gap: 14px;
  }
  .card--front .brand-mark { left: 546px; top: 40px; width: 170px; }
  .card--back .brand-mark  { left: 263px; top: 130px; width: 220px; }
  .brand-mark__circle { border-radius: 50%; }
  .card--front .brand-mark__circle { width: 96px; height: 96px; background: var(--crest-grey); }
  .card--back .brand-mark__circle  { width: 124px; height: 124px; background: var(--white); }
  .brand-mark__name { font-weight: 700; letter-spacing: 4px; }
  .card--front .brand-mark__name { font-size: 26px; color: var(--crest-grey); }
  .card--back .brand-mark__name  { font-size: 32px; color: var(--white); }

  /* person */
  .person-accent {
    position: absolute; left: 0; top: 228px; width: 10px; height: 59px; background: var(--maroon);
  }
  .person {
    position: absolute; left: 29px; top: 228px;
  }
  .person__name { font-weight: 600; font-size: 27px; color: var(--maroon); line-height: 1.15; }
  .person__title { font-size: 20px; color: var(--ink); line-height: 1.2; }

  .contact {
    position: absolute; font-size: 19.5px; line-height: 30px; color: var(--ink-soft);
  }
  .contact--address { left: 29px; top: 288px; }
  .contact--reach { left: 333px; top: 318px; }
  .contact__label { color: var(--maroon); font-weight: 700; }

  .back-web {
    position: absolute; left: 0; right: 0; top: 376px;
    text-align: center; font-size: 19.5px; color: var(--white);
  }
</style>
</head>
<body>
<div class="canvas">
  <section class="card card--front">
    <div class="company-mark">
      <div class="company-mark__square"></div>
      <div class="company-mark__name">DRV Ventures Inc.</div>
    </div>

    <div class="brand-mark">
      <div class="brand-mark__circle"></div>
      <div class="brand-mark__name">TORVAN</div>
    </div>

    <div class="person-accent"></div>
    <div class="person">
      <div class="person__name">Marisol Depree</div>
      <div class="person__title">CEO</div>
    </div>

    <address class="contact contact--address" style="font-style:normal">
      Ground floor<br>
      Lindell Plaza Suite 2734<br>
      George Town,Grand Cayman<br>
      Cayman Islands,KY1-4823
    </address>

    <div class="contact contact--reach">
      <span class="contact__label">Mobile:</span>1 555 4180736<br>
      m.depree@drvventuresinc.example<br>
      www.drvventuresinc.example
    </div>
  </section>

  <section class="card card--back">
    <div class="brand-mark">
      <div class="brand-mark__circle"></div>
      <div class="brand-mark__name">TORVAN</div>
    </div>
    <div class="back-web">www.drvventuresinc.example</div>
  </section>
</div>
</body>
</html>
```